Tolbek cards

I want a simple business card that pops.
Logo on one side.
On side two i want.
"Are you thinking about a new building on your property, or renovating an existing structure? Contact".....
Owners Name: Dale Whitacre
Owners Phone number: 610-555-0187
Address:4076 Copper Ridge RD, Millbrook, OH 43876
Committed to Quality, Service, and Integrity

```html
<!DOCTYPE html>
<html lang="en">
<head>
<meta charset="utf-8">
<title>Tolbek Builders LLC – Business Card</title>
<link rel="stylesheet" href="https://fonts.googleapis.com/css2?family=Poppins:wght@400;600;800&display=swap">
<style>
  :root {
    --brown: #422e1c;
    --brown-deep: #5c3d24;
    --tan: #a38d74;
    --white: #ffffff;
    --stage: #f0f0f0;
    --ink: #1b1410;
  }
  * { box-sizing: border-box; margin: 0; padding: 0; }
  html, body { width: 1200px; height: 990px; overflow: hidden; }
  body {
    background: var(--stage);
    font-family: "Poppins", sans-serif;
    position: relative;
  }
  .card {
    position: absolute;
    left: 244px;
    width: 712px;
    height: 406px;
    border-radius: 51px;
    overflow: hidden;
    box-shadow: 0 14px 26px rgba(0,0,0,0.28);
  }
  .card-front { top: 68px; background: var(--brown); }
  .card-back  { top: 516px; background: var(--white); }

  /* Brand blocks */
  .brand {
    position: absolute;
    text-align: center;
    font-weight: 800;
    text-transform: uppercase;
    white-space: nowrap;
  }
  .brand-square { position: absolute; left: 50%; transform: translateX(-50%); }
  .brand-name, .brand-sub { position: absolute; left: 0; right: 0; }

  .front-brand { left: 0; right: 0; top: 0; height: 406px; color: var(--white); }
  .front-brand .brand-square { top: 80px; width: 96px; height: 96px; background: var(--white); }
  .front-brand .brand-name { top: 218px; font-size: 82px; line-height: 82px; letter-spacing: -1px; }
  .front-brand .brand-sub { top: 300px; font-size: 28px; line-height: 30px; letter-spacing: 1px; }

  .back-brand { left: 20px; top: 0; width: 210px; height: 200px; color: var(--brown); }
  .back-brand .brand-square { top: 28px; width: 70px; height: 70px; background: var(--brown); }
  .back-brand .brand-name { top: 106px; font-size: 48px; line-height: 50px; letter-spacing: -1px; }
  .back-brand .brand-sub { top: 154px; font-size: 17px; line-height: 20px; letter-spacing: 0.5px; }

  .pitch {
    position: absolute; right: 27px; top: 20px;
    text-align: right; font-size: 19px; line-height: 24px; color: var(--ink); font-weight: 400;
    white-space: nowrap;
  }
  .info-band {
    position: absolute; left: 0; top: 203px; width: 838px; height: 203px;
    background: var(--brown);
  }
  .corner-block {
    position: absolute; left: 483px; top: 203px; width: 229px; height: 203px;
    background: linear-gradient(135deg, var(--tan), var(--brown-deep));
  }
  .owner {
    position: absolute; left: 26px; top: 203px; color: var(--white);
  }
  .owner-name { font-size: 30px; font-weight: 600; line-height: 36px; margin-top: 5px; }
  .owner-role { font-size: 16px; line-height: 20px; letter-spacing: 0.5px; }
  .motto { font-size: 17px; line-height: 22px; margin-top: 12px; letter-spacing: 0.3px; }
  .contact { list-style: none; margin-top: 14px; }
  .contact li {
    display: flex; align-items: center; gap: 10px;
    font-size: 17px; line-height: 26px; letter-spacing: 0.5px;
  }
  .contact .icon {
    width: 21px; height: 21px; border-radius: 50%; background: var(--white);
    display: flex; align-items: center; justify-content: center; flex: none;
  }
  .contact .phone-line { padding-left: 2px; gap: 15px; }
</style>
</head>
<body>
  <section class="card card-front">
    <div class="brand front-brand">
      <div class="brand-square"></div>
      <div class="brand-name">Tolbek</div>
      <div class="brand-sub">Builders LLC</div>
    </div>
  </section>

  <section class="card card-back">
    <div class="brand back-brand">
      <div class="brand-square"></div>
      <div class="brand-name">Tolbek</div>
      <div class="brand-sub">Builders LLC</div>
    </div>

    <p class="pitch">"Are you thinking about a new building<br>on your property, or renovating an<br>existing structure? Contact".....</p>

    <div class="info-band"></div>
    <div class="corner-block" role="img" aria-label="Large brand symbol in tan-to-brown tones"></div>

    <div class="owner">
      <h1 class="owner-name">Dale Whitacre</h1>
      <p class="owner-role">Owners</p>
      <p class="motto">Committed to Quality,<br>Service, and Integrity</p>
      <ul class="contact">
        <li class="phone-line">
          <span class="icon">
            <svg width="13" height="13" viewBox="0 0 24 24" fill="var(--brown)"><path d="M6.6 10.8a15.1 15.1 0 0 0 6.6 6.6l2.2-2.2a1 1 0 0 1 1-.25 11.4 11.4 0 0 0 3.6.57 1 1 0 0 1 1 1V20a1 1 0 0 1-1 1A17 17 0 0 1 3 4a1 1 0 0 1 1-1h3.5a1 1 0 0 1 1 1c0 1.25.2 2.45.57 3.570a1 1 0 0 1-.25 1z"/></svg>
          </span>
          610-555-0187
        </li>
        <li>
          <span class="icon">
            <svg width="12" height="14" viewBox="0 0 24 28" fill="var(--brown)"><path d="M12 0a10 10 0 0 0-10 10c0 7.5 10 18 10 18s10-10.5 10-18A10 10 0 0 0 12 0zm0 14a4 4 0 1 1 0-8 4 4 0 0 1 0 8z"/></svg>
          </span>
          4076 Copper Ridge RD, Millbrook, OH 43876
        </li>
      </ul>
    </div>
  </section>
</body>
</html>
```